National Sales - Pick Up Truck Dealer

We need a logo design for a new vehicle dealership based in Sydney, Norland. The business name is Coastal Iron Haulers Motor Co. We will be selling American 'trucks/pick up trucks' like KRV, Torvan, Blaxer, Morrow T420, Kenzo Raptors, Morrow T640 and the likes.

These vehicles are a luxury option and we would like the logo to be strong, luxurious and masculine.Colours will be black and red or black and blue with the option of grey and white.

Target Market(s)

Men

Industry/Entity Type

Car Dealer

Contact Information for Business Card

Dennis Harlowe
Managing Director
0412 639 274
den@qelvtrk.com.au

Level 3, Brindle Parkway
17 Pemberly Lane
Wexley Ridge
VIC
Norland
Licence No: MD493152

Back of the card

qelvtrk.com.au

Font styles to use
Sans Serif

Colors

Designer to choose colors to be used in the design.

Requirements
Must have
• The company logo that is in the attachments, you can choose from the three which one you would like to work with. Must have vehicle images ....Please look at the attachments as they show examples of what we like and also provides potential images. If you choose to put an image on the front even if it is just the front of the vehicle can you please use the Black KRV Sorrento. Must have all details from the business card details section front and back
Nice to have
• N/A
Should not have
• No cars or standard trucks, please refer to the attached images to understand the product . Should not have any new logos or branding. No other colours besides what is in the logo you choose.

```html
<!DOCTYPE html>
<html lang="en">
<head>
<meta charset="utf-8">
<title>Coastal Iron Haulers Motor Co – Business Card</title>
<link rel="stylesheet" href="https://fonts.googleapis.com/css2?family=Roboto:wght@400;500;700&family=Open+Sans:wght@400;600&display=swap">
<style>
  :root {
    --card-dark: #232325;
    --stripe-black: #111112;
    --brand-red: #d0232a;
    --deep-red: #8f161a;
    --mid-red: #b41e25;
    --silver-light: #f2f2f3;
    --silver-mid: #c9c9cb;
    --silver-dark: #9a9a9c;
    --text-light: #ffffff;
    --text-dark: #1b1b1d;
    --page: #ffffff;
  }
  * { box-sizing: border-box; margin: 0; padding: 0; }
  html, body {
    width: 1200px; height: 1200px; overflow: hidden;
    background: var(--page);
  }
  .canvas { position: relative; width: 1200px; height: 1200px; }

  .card {
    position: absolute; left: 234px; width: 733px; height: 426px; overflow: hidden;
  }
  .card--front { top: 126px; background: var(--card-dark); }
  .card--back {
    top: 624px;
    background: radial-gradient(ellipse at 50% 50%, var(--mid-red) 0%, var(--mid-red) 30%, var(--deep-red) 100%);
  }

  .front-shapes { position: absolute; inset: 0; width: 100%; height: 100%; }

  .name-block {
    position: absolute; left: 0; top: 69px; width: 267px; height: 63px;
    background: var(--brand-red); padding: 10px 0 0 50px;
    font-family: "Roboto", sans-serif; color: var(--text-dark);
  }
  .name-block__name { font-size: 22px; font-weight: 500; line-height: 1; white-space: nowrap; }
  .name-block__title { font-size: 14.5px; font-weight: 500; margin-top: 4px; }

  .contact-list {
    position: absolute; left: 64px; top: 158px; list-style: none;
    font-family: "Open Sans", sans-serif; font-size: 15px; color: var(--text-light);
  }
  .contact-item { display: flex; align-items: center; margin-bottom: 20px; }
  .contact-item__icon { width: 24px; height: 24px; margin-right: 17px; flex: none; }
  .contact-item__text { line-height: 18.5px; }
  .contact-item--address { margin-bottom: 26px; }

  .brand-lockup {
    position: absolute; left: 400px; top: 88px; width: 290px; text-align: center;
    font-family: "Roboto", sans-serif; font-weight: 700; color: var(--text-dark);
    text-transform: uppercase; line-height: 1.1; font-size: 21px; letter-spacing: 0.4px;
  }

  .vehicle-photo {
    position: absolute; left: 378px; top: 172px; width: 318px; height: 118px;
    border-radius: 10px;
    background: linear-gradient(180deg, #4a4b50 0%, #2c2d31 60%, #1c1c1f 100%);
  }

  .back-emblem { position: absolute; left: 206px; top: 53px; width: 320px; height: 320px; }
  .back-url {
    position: absolute; left: 0; right: 0; top: 192px; text-align: center;
    font-family: "Open Sans", sans-serif; font-weight: 600; font-size: 32px;
    color: var(--brand-red); letter-spacing: -0.3px;
  }
</style>
</head>
<body>
<main class="canvas">

  <section class="card card--front" aria-label="Business card front">
    <svg class="front-shapes" viewBox="0 0 916 533" preserveAspectRatio="none" aria-hidden="true">
      <defs>
        <radialGradient id="silver-panel" cx="0.6" cy="0.3" r="0.8">
          <stop offset="0" stop-color="#f2f2f3"/>
          <stop offset="0.55" stop-color="#c9c9cb"/>
          <stop offset="1" stop-color="#9a9a9c"/>
        </radialGradient>
        <linearGradient id="red-panel" x1="0" y1="0" x2="1" y2="1">
          <stop offset="0" stop-color="#d0232a"/>
          <stop offset="1" stop-color="#8f161a"/>
        </linearGradient>
      </defs>
      <polygon points="455,0 470,0 395,240 555,533 540,533 375,240" fill="#111112"/>
      <polygon points="470,0 505,0 450,275 916,533 555,533 395,240" fill="url(#red-panel)"/>
      <polygon points="505,0 916,0 916,533 450,275" fill="url(#silver-panel)"/>
    </svg>

    <div class="name-block">
      <p class="name-block__name">DENNIS HARLOWE</p>
      <p class="name-block__title">Managing Director</p>
    </div>

    <ul class="contact-list">
      <li class="contact-item">
        <svg class="contact-item__icon" viewBox="0 0 24 24" aria-hidden="true">
          <path d="M3 8c0-2 4-3.5 9-3.5S21 6 21 8v1.5h-4.5V8h-9v1.5H3z" fill="var(--brand-red)"/>
          <path d="M7 10h10l3 8v2H4v-2z" fill="var(--brand-red)"/>
          <circle cx="12" cy="15" r="2.2" fill="var(--card-dark)"/>
        </svg>
        <span class="contact-item__text">0412 639 274</span>
      </li>
      <li class="contact-item">
        <svg class="contact-item__icon" viewBox="0 0 24 24" aria-hidden="true">
          <rect x="2" y="5" width="20" height="14" fill="none" stroke="var(--brand-red)" stroke-width="2"/>
          <path d="M2.5 5.5 12 13l9.5-7.5" fill="none" stroke="var(--brand-red)" stroke-width="2"/>
        </svg>
        <span class="contact-item__text">den@qelvtrk.com.au</span>
      </li>
      <li class="contact-item contact-item--address">
        <svg class="contact-item__icon" viewBox="0 0 24 24" aria-hidden="true">
          <path d="M12 2a6.5 6.5 0 0 0-6.5 6.5C5.5 13.5 12 22 12 22s6.5-8.5 6.5-13.5A6.5 6.5 0 0 0 12 2z" fill="var(--brand-red)"/>
          <circle cx="12" cy="8.5" r="2.4" fill="var(--card-dark)"/>
        </svg>
        <span class="contact-item__text">Level 3, Brindle Parkway,<br>17 Pemberly Lane,<br>Wexley Ridge, VIC,<br>Norland</span>
      </li>
      <li class="contact-item">
        <svg class="contact-item__icon" viewBox="0 0 24 24" aria-hidden="true">
          <rect x="4" y="2" width="16" height="20" fill="none" stroke="var(--brand-red)" stroke-width="1.8"/>
          <path d="M7 6h10M7 9h10M7 12h10M7 15h6" stroke="var(--brand-red)" stroke-width="1.6"/>
          <rect x="14" y="16" width="4" height="6" fill="var(--brand-red)"/>
        </svg>
        <span class="contact-item__text">Licence No:&nbsp; MD493152</span>
      </li>
    </ul>

    <p class="brand-lockup">Coastal Iron Haulers<br>Motor Co</p>

    <div class="vehicle-photo" role="img" aria-label="Photo of a Black KRV Sorrento flanked by two pickup trucks, front view"></div>
  </section>

  <section class="card card--back" aria-label="Business card back">
    <svg class="back-emblem" viewBox="0 0 320 320" aria-hidden="true">
      <circle cx="160" cy="160" r="155" fill="none" stroke="var(--silver-mid)" stroke-width="8"/>
      <circle cx="160" cy="160" r="142" fill="var(--card-dark)"/>
    </svg>
    <p class="back-url">qelvtrk.com.au</p>
  </section>

</main>
</body>
</html>
```